New Business Card Design Project

I need a design for business cards, i am an electrical business called "Corvane Electrical and Communications" i need the cards to be double sided with the company logo on the back (attached) the front needs to say my company name, web site, email address, telephone number, and ABN number and electrical license number. I am open to different arrangements of the information but would like the background to be incorporating something electrical or something that looks smart. open to all additional ideas also.

The company colours are orange and grey see logo attached.

Business Name: Corvane Electrical and Communications
Website: corvaneelectricalandcomms.example.com.au
Email: brent@corvaneelectricalandcomms.example.com.au
Telephone(mobile): 0481209736
ABN: 71208349162
Lic No: 418273D

Target Market(s)

Business entities, Project Managers, Accounts, Clients

Industry/Entity Type

Electrician

Contact Information for Business Card

I need a design for business cards, i am an electrical business called "Corvane Electrical and Communications" i need the cards to be double sided with the company logo on the back (attached) the front needs to say my company name

Font styles to use
Serif
Sans Serif

Colors
f37122
5c5c5c

Requirements
Must have
• Must have the Logo on the back open to different ways of it being on the back but had in mind to keep it central but again open to other options
Nice to have
• A real modern cool background that is eye catching yet contemporary
Should not have
• No backgrounds of a light bulb or plug or anything like that

```html
<!DOCTYPE html>
<html lang="en">
<head>
<meta charset="utf-8">
<title>Corvane Electrical and Communications – Business Card</title>
<link rel="stylesheet" href="https://fonts.googleapis.com/css2?family=Exo+2:wght@600;700&family=Arimo:wght@400&family=Open+Sans:wght@400;600&display=swap">
<style>
  :root {
    --stage: #3b3b3c;
    --card: #58585a;
    --amber: #f6a81d;
    --white: #ffffff;
    --soft-white: #eeeeee;
  }
  html, body {
    margin: 0;
    padding: 0;
    width: 1105px;
    height: 1200px;
    overflow: hidden;
    background: var(--stage);
  }
  .canvas {
    position: relative;
    width: 1105px;
    height: 1200px;
  }
  .card {
    position: absolute;
    left: 192px;
    width: 720px;
    height: 410px;
    background: var(--card);
    overflow: hidden;
  }
  .card--front { top: 147px; }
  .card--back { top: 602px; }

  .edge-tab {
    position: absolute;
    left: 0;
    top: 104px;
    width: 11px;
    height: 34px;
    background: var(--amber);
    border-radius: 0 17px 17px 0;
  }
  .holder {
    position: absolute;
    left: 37px;
    top: 100px;
  }
  .holder__name {
    margin: 0;
    font-family: "Exo 2", sans-serif;
    font-weight: 700;
    font-size: 27px;
    line-height: 32px;
    color: var(--amber);
  }
  .holder__role {
    margin: 0;
    font-family: "Exo 2", sans-serif;
    font-weight: 600;
    font-size: 19px;
    line-height: 24px;
    color: var(--white);
  }
  .details {
    position: absolute;
    left: 37px;
    top: 176px;
    font-family: "Arimo", sans-serif;
    color: var(--soft-white);
  }
  .details p { margin: 0; }
  .details__reg {
    font-size: 18px;
    line-height: 27px;
  }
  .details__mobile {
    margin-top: 8px !important;
    font-size: 19px;
    line-height: 27px;
  }
  .details__label {
    font-family: "Exo 2", sans-serif;
    font-weight: 700;
    color: var(--amber);
  }
  .details__web {
    font-size: 14px;
    line-height: 27px;
  }

  .brand {
    position: absolute;
    display: flex;
    align-items: center;
  }
  .brand--front {
    right: 40px;
    top: 232px;
    gap: 10px;
  }
  .brand--back {
    left: 0;
    right: 0;
    top: 150px;
    gap: 14px;
    justify-content: center;
  }
  .brand__dot {
    border-radius: 50%;
    background: var(--amber);
    flex: none;
  }
  .brand--front .brand__dot { width: 16px; height: 16px; }
  .brand--back .brand__dot { width: 22px; height: 22px; }
  .brand__name {
    font-family: "Exo 2", sans-serif;
    font-weight: 600;
    white-space: nowrap;
  }
  .brand--front .brand__name {
    font-size: 44px;
    line-height: 50px;
    letter-spacing: 1px;
    color: var(--white);
  }
  .brand--back .brand__name {
    font-size: 64px;
    line-height: 70px;
    letter-spacing: 2px;
    color: var(--amber);
  }

  .back-url {
    position: absolute;
    left: 0;
    right: 0;
    top: 328px;
    margin: 0;
    text-align: center;
    font-family: "Open Sans", sans-serif;
    font-size: 17px;
    letter-spacing: 1.4px;
    color: var(--white);
  }
</style>
</head>
<body>
<main class="canvas">
  <section class="card card--front" aria-label="Card front">
    <div class="edge-tab"></div>
    <div class="holder">
      <p class="holder__name">Dale Harper</p>
      <p class="holder__role">CEO/Founder</p>
    </div>
    <div class="details">
      <p class="details__reg">ABN: 71208349162</p>
      <p class="details__reg">Lic No: 418273D</p>
      <p class="details__mobile"><span class="details__label">Mobile :</span> 0481209736</p>
      <p class="details__web">brent@corvaneelectricalandcomms.example.com.au</p>
      <p class="details__web">corvaneelectricalandcomms.example.com.au</p>
    </div>
    <div class="brand brand--front">
      <span class="brand__dot"></span>
      <span class="brand__name">CORVANE</span>
    </div>
  </section>

  <section class="card card--back" aria-label="Card back">
    <div class="brand brand--back">
      <span class="brand__dot"></span>
      <span class="brand__name">CORVANE</span>
    </div>
    <p class="back-url">www.corvaneelectricalandcomms.example.com.au</p>
  </section>
</main>
</body>
</html>
```